American cannabis tech company business card design

Pavrel.com is seeking a modern, professional, and brand-aligned business card that represents our company and its core values: Mission, Story, Values, and Impact. As an innovative cannabis company, we want a business card that is not only visually appealing but also serves as a representation of who we are and what we stand for.

Project Scope: Design a double-sided business card that integrates our brand identity and core values. Incorporate our key brand elements, ensuring a sleek and contemporary aesthetic. Visually reflect our core values (Mission, Story, Values, Impact) in a way that is engaging yet professional.

Target Market(s)

Vendors, third parties,

Contact Information for Business Card

Contact details (name, title, email, phone, website, etc.)

Font styles to use
Other font styles liked:
• Caslon, Centra

Colors

Designer to choose colors to be used in the design.

Requirements
Must have
• Pavrel.com logo and branding A creative yet clean way to integrate our core values (Mission, Story, Values, Impact) Modern typography and a well-structured layout
Nice to have
• forest green, grey, white, black
Should not have
• references to marijuana, leafs, plants, or related product

```html
<!DOCTYPE html>
<html lang="en">
<head>
<meta charset="utf-8">
<title>Pavrel Business Card</title>
<link rel="stylesheet" href="https://fonts.googleapis.com/css2?family=Poppins:wght@300;400;600;700&display=swap">
<style>
  :root {
    --page-bg: #d9d2c6;
    --panel-dark: #1f2620;
    --panel-mid: #2f3a31;
    --frost-light: #e6e4df;
    --frost-mid: #c9c4bb;
    --frost-warm: #d8c6b4;
    --text-light: #e9e3d8;
    --text-soft: #cfc7b9;
    --icon-fill: #cbbfae;
    --logo-ink: #0f1410;
    --edge-line: #0b0e0b;
  }
  * { margin: 0; padding: 0; box-sizing: border-box; }
  html, body { width: 1200px; height: 970px; overflow: hidden; }
  body {
    background: var(--page-bg);
    font-family: "Poppins", sans-serif;
    position: relative;
  }
  .card {
    position: absolute;
    left: 100px;
    top: 200px;
    width: 1000px;
    height: 570px;
    border-radius: 22px;
    overflow: hidden;
    background: linear-gradient(160deg, var(--frost-light) 0%, var(--frost-mid) 55%, var(--frost-warm) 100%);
    box-shadow: 0 18px 40px rgba(40, 32, 20, 0.25);
  }
  .card-shapes { position: absolute; inset: 0; }
  .contact-side {
    position: absolute;
    left: 55px;
    top: 80px;
    color: var(--text-light);
  }
  .holder-name {
    font-weight: 600;
    font-size: 31px;
    letter-spacing: 0.5px;
    line-height: 1.1;
  }
  .holder-title {
    font-weight: 300;
    font-size: 24px;
    color: var(--text-soft);
    margin-top: 2px;
  }
  .address {
    margin-top: 105px;
    font-weight: 300;
    font-size: 24px;
    line-height: 31px;
    color: var(--text-soft);
  }
  .contact-list {
    list-style: none;
    margin-top: 30px;
  }
  .contact-list li {
    display: flex;
    align-items: center;
    gap: 16px;
    font-weight: 300;
    font-size: 24px;
    line-height: 34px;
    color: var(--text-soft);
  }
  .contact-icon { width: 28px; height: 28px; flex: none; }
  .brand-name {
    position: absolute;
    left: 570px;
    top: 225px;
    width: 380px;
    text-align: center;
    font-weight: 700;
    font-size: 82px;
    letter-spacing: 1px;
    color: var(--logo-ink);
    line-height: 1;
  }
</style>
</head>
<body>
  <div class="card">
    <svg class="card-shapes" width="1000" height="570" viewBox="0 0 1000 570">
      <defs>
        <radialGradient id="panelShade" cx="0.45" cy="0.4" r="0.7">
          <stop offset="0" stop-color="var(--panel-mid)"/>
          <stop offset="1" stop-color="var(--panel-dark)"/>
        </radialGradient>
      </defs>
      <path class="edge-accent" d="M535,0 C448,180 448,390 535,570 H522 C438,390 438,180 522,0 Z" fill="var(--edge-line)"/>
      <path class="dark-panel" d="M0,0 H518 C432,180 432,390 518,570 H0 Z" fill="url(#panelShade)"/>
      <circle class="panel-notch" cx="0" cy="112" r="31" fill="var(--icon-fill)"/>
    </svg>

    <div class="contact-side">
      <h1 class="holder-name">DANIEL R. HAYES</h1>
      <p class="holder-title">Director</p>
      <p class="address">4820 W. Cedar Ave.<br>Suite 210<br>Tempe, Arizona 85281</p>
      <ul class="contact-list">
        <li>
          <svg class="contact-icon" viewBox="0 0 28 28"><rect width="28" height="28" rx="4" fill="var(--icon-fill)"/><path d="M7 11 C7 8 21 8 21 11 L19 12.5 L17 11 H11 L9 12.5 Z M10 13 H18 L20 20 H8 Z" fill="var(--panel-dark)"/><circle cx="14" cy="16.5" r="2" fill="var(--icon-fill)"/></svg>
          <span>+1 555 -210-4837</span>
        </li>
        <li>
          <svg class="contact-icon" viewBox="0 0 28 28"><rect width="28" height="28" rx="4" fill="var(--icon-fill)"/><rect x="5" y="8" width="18" height="12" fill="none" stroke="var(--panel-dark)" stroke-width="1.6"/><path d="M5 8 L14 15 L23 8 M5 20 L11 13.5 M23 20 L17 13.5" fill="none" stroke="var(--panel-dark)" stroke-width="1.4"/></svg>
          <span>team@pavrel.com</span>
        </li>
        <li>
          <svg class="contact-icon" viewBox="0 0 28 28"><rect width="28" height="28" rx="4" fill="var(--icon-fill)"/><circle cx="14" cy="14" r="8" fill="none" stroke="var(--panel-dark)" stroke-width="1.5"/><ellipse cx="14" cy="14" rx="3.5" ry="8" fill="none" stroke="var(--panel-dark)" stroke-width="1.3"/><path d="M6 14 H22 M7.5 10 H20.5 M7.5 18 H20.5" stroke="var(--panel-dark)" stroke-width="1.2"/></svg>
          <span>www.PAVREL.com</span>
        </li>
      </ul>
    </div>

    <div class="brand-name">PAVREL</div>
  </div>
</body>
</html>
```